Tuition Center Website

We need a new web site for a tutoring company based in sydney.

We only teach senior highschool students and pride ourselves on building the students abilities to think their way through life.

I would like a bright and vibrant website that looks professional and modern.
It needs to look simple and neat but also have the functionality we need.
Images and flash would be good.

Please keep in mind that the site must be appealing to a younger audience.

We need a multipage website with the following navigation bars:

1.Home (As logo not "home" button)
I would like a news box/ticker somewhere that can stream our chatterbook and pipstream feeds and also any news updates we want to put up.
Subscribe to newsletter button.

2. About us.
This needs to be a pull down into:
-What we do
-Why we do it
-How we do it

3. Courses
Pulldown into:
-Maths
-English
-Science
(we may need to attach extra pages behind these e.g. Courses/Science/Physics or Courses/Science/Chemistry and possibly add a link to a new zandlo form)

4. Inspired
This page is like a blog page where we can upload videos, links to articles that we find to be inspiring and hopefully will inspire others.

5. Inspire
This is a recruitment page. Only content here.

6. Contact us.
Mapquill map widget and a 'contact us' form

* Our branding requires green close to #12FF3D

***Please have a look at the current website.
@ www.velmorlearning.com.au

Thanks everybody hope the revision of my brief is better and more informative than my last one

Target Market(s)

senior highschool students aged 15-19, parents ( to a lesser degree)

Industry/Entity Type

It Company

Requirements
Must have
• Ability to change content on pages.

The green doesn't have to be everywhere, but it must be obvious that it is our colour.

Nice to have
• Sites with a nicer mix of images and flash will be given more consideration. But then again, if you amaze us, you amaze us and we will go with your design.
Should not have
• Should stay away from ocre, brown colours and serif fonts.

```html
<!DOCTYPE html>
<html lang="en">
<head>
<meta charset="utf-8">
<title>Velmor Learning</title>
<link rel="stylesheet" href="https://fonts.googleapis.com/css2?family=Figtree:wght@400;500;600;700&family=Open+Sans:wght@400;600;700&family=Gochi+Hand&display=swap">
<style>
:root{
  --green:#8fd400;
  --green-dark:#5a9e12;
  --ink:#2b2b2b;
  --grey:#8a8a8a;
  --grey-light:#a5a5a5;
  --page-bg:#ececec;
  --panel:#f3f3f3;
  --line:#dcdcdc;
  --black:#0c0c0c;
  --link:#1aa3d8;
  --news:#3a5c8c;
}
*{box-sizing:border-box;margin:0;padding:0}
html,body{width:897px;height:1200px;overflow:hidden}
body{background:var(--page-bg);font-family:"Figtree",sans-serif;color:var(--ink);position:relative}
.site{position:absolute;left:90px;top:28px;width:717px;height:1146px;background:#fff;box-shadow:0 0 6px rgba(0,0,0,.12)}
.abs{position:absolute}

/* header */
.brand{left:44px;top:26px;display:flex;align-items:center;gap:8px}
.brand-mark{width:22px;height:22px;background:var(--green)}
.brand-name{font-size:19px;font-weight:600;color:var(--ink);line-height:1.05}
.nav{left:283px;top:53px;width:417px;height:31px;background:#2e2e2e;border-radius:3px;border:2px solid #1c1c1c;display:flex;align-items:center;padding:0 5px;gap:0}
.nav a{font-size:11px;font-weight:500;color:#fff;text-decoration:none;padding:5px 12px;border-radius:2px}
.nav a.active{background:var(--green);color:#1e3b00}

/* hero */
.hero{left:0;top:109px;width:717px;height:285px;background:linear-gradient(90deg,#6f7a78 0%,#8d9688 35%,#a47a5c 60%,#6a7d45 100%)}
.hero-shade{left:0;top:109px;width:420px;height:285px;background:linear-gradient(90deg,rgba(90,95,90,.55),rgba(90,95,90,0))}
.hero-title{left:32px;top:150px;font-size:25px;font-weight:500;line-height:28px;color:#262626}
.hero-title .accent{color:var(--green)}
.hero-copy{left:32px;top:240px;width:300px;font-size:11px;line-height:14.5px;color:#fff}
.btn-enquire{left:32px;top:301px;width:115px;height:31px;background:linear-gradient(#2a2a2a,#000);color:#fff;font-size:11.5px;font-weight:700;display:flex;align-items:center;justify-content:center;border-radius:2px;letter-spacing:-.2px}
.dots{left:32px;top:372px;display:flex;gap:8px}
.dots span{width:8px;height:8px;border-radius:50%;background:#111}
.dots span.on{background:#fff}

/* intro */
.intro-title{left:24px;top:431px;font-size:16px;font-weight:500;color:#333}
.intro-copy{left:24px;top:465px;width:490px;font-size:11.2px;line-height:16.5px;color:var(--grey)}
.btn-register{left:22px;top:524px;width:84px;height:23px;background:linear-gradient(#fafafa,#e2e2e2);border:1px solid #d5d5d5;font-size:9.5px;color:#333;display:flex;align-items:center;justify-content:center;border-radius:2px}
.intro-art{left:528px;top:428px;width:144px;height:120px;background:radial-gradient(ellipse at center,#e6f4d4 0%,#f6fbef 60%,#fff 100%)}

/* panels */
.panels{left:0;top:588px;width:717px;height:155px;background:linear-gradient(#f7f7f7,#ebebeb);border-top:1px solid var(--line);display:flex}
.panel{flex:1;padding:18px 19px 0;border-right:1px solid var(--line);position:relative}
.panel:last-child{border-right:none}
.panel h3{font-size:14px;font-weight:500;color:#222}
.quote{display:flex;gap:10px;margin-top:14px}
.avatar{width:44px;height:44px;flex:none;background:linear-gradient(#b37a5a,#3e3a3a)}
.quote p{font-size:9px;line-height:13.3px;color:var(--grey);font-family:"Open Sans",sans-serif}
.cite{margin-top:10px;font-size:9px;color:#555;font-family:"Open Sans",sans-serif}
.cite b{color:#222}
.trial-box{margin-top:14px;width:203px;height:45px;background:#2c2c2c;color:#fff;padding:4px 8px;position:relative}
.trial-box .l1{font-size:13px}
.trial-box .l2{position:absolute;right:12px;bottom:4px;font-size:13px}
.trial-box .l2 b{color:var(--green);font-style:italic;font-size:16px;font-weight:700}
.trial-note{margin-top:10px;font-size:9px;color:var(--grey);font-family:"Open Sans",sans-serif}
.trial-link{margin-top:8px;font-size:10px;font-weight:600;color:#333;font-family:"Open Sans",sans-serif}
.news-head{display:flex;align-items:center;gap:10px}
.news-item{display:flex;gap:8px;margin-top:13px}
.news-date{font-size:15px;line-height:14px;color:#222;flex:none}
.news-date sup{font-size:8px;font-weight:700}
.news-date small{display:block;font-size:10px;margin-top:2px}
.news-item h4{font-size:12px;font-weight:500;color:var(--news)}
.news-item p{font-size:9px;line-height:13.5px;color:var(--grey-light);margin-top:3px;font-family:"Open Sans",sans-serif}

/* beliefs */
.beliefs{left:0;top:743px;width:717px;height:203px;display:flex;padding:32px 22px 0 28px}
.belief{flex:1}
.belief-head{display:flex;align-items:center;gap:12px}
.belief-head h3{font-family:"Gochi Hand",cursive;font-weight:400;font-size:20px;color:var(--green-dark)}
.belief ul{list-style:none;margin:24px 0 0 10px}
.belief li{display:flex;gap:6px;font-size:10.5px;line-height:12px;color:#555;margin-bottom:9px;max-width:195px}
.belief li svg{flex:none;margin-top:-1px}

/* tweet */
.tweet{left:0;top:918px;width:717px;height:36px;background:#ebebeb;display:flex;align-items:center;padding-left:50px;gap:8px;font-family:"Open Sans",sans-serif;font-size:9.5px;color:#222}
.tweet .dot{width:18px;height:18px;border-radius:50%;background:var(--link)}
.tweet a{color:var(--link);text-decoration:none}

/* footer */
.footer{left:0;top:954px;width:717px;height:182px;background:#f6f6f6;font-family:"Open Sans",sans-serif}
.fcol{position:absolute;top:16px}
.fcol h4{font-family:"Figtree",sans-serif;font-size:14.5px;font-weight:500;color:#555;margin-bottom:8px}
.fcol dt{font-size:9.5px;font-weight:600;color:#999}
.fcol dd{font-size:9.5px;color:#a0a0a0;margin-bottom:8px;letter-spacing:.3px}
.fcol li{list-style:none;font-size:9.3px;line-height:13.6px;color:#a5a5a5;letter-spacing:.3px}
.fcol p{font-size:9.3px;line-height:13.5px;color:#999;letter-spacing:.3px}
.fcol .name{font-size:9.5px;font-weight:700;color:var(--green);margin:3px 0 12px}
.email-field{margin-top:14px;width:148px;height:22px;border:1px solid #ccc;border-radius:3px;background:#fff;font-size:9px;color:#aaa;padding:5px 9px}
.btn-sub{margin-top:14px;width:67px;height:19px;background:#111;color:#fff;border-radius:3px;font-size:9px;font-weight:700;display:flex;align-items:center;justify-content:center;font-family:"Figtree",sans-serif}

/* bottom bar */
.bottom{left:0;top:1108px;width:717px;height:38px;background:var(--black);display:flex;align-items:center;justify-content:space-between;padding:0 19px 0 28px;font-size:10px;color:#fff}
.bottom nav{display:flex;gap:12px}
</style>
</head>
<body>
<div class="site">
  <div class="abs brand">
    <span class="brand-mark"></span>
    <span class="brand-name">velmor<br>learning</span>
  </div>
  <nav class="abs nav">
    <a class="active">Home</a><a>About Us</a><a>Courses</a><a>Inspired</a><a>Inspire</a><a>Contact Us</a>
  </nav>

  <div class="abs hero" role="img" aria-label="Photo of three smiling students sharing a laptop outdoors, with a blurred campus building behind"></div>
  <div class="abs hero-shade"></div>
  <h1 class="abs hero-title">Inspiring Minds.<br>Nurturing Potential.<br><span class="accent">Equipping Success.</span></h1>
  <p class="abs hero-copy">The HSC help you need, in the years you need it. We offer small classes, individualised attention and genuine care for each student. It's different - in a good way.</p>
  <div class="abs btn-enquire">ENQUIRE NOW</div>
  <div class="abs dots"><span></span><span class="on"></span><span></span></div>

  <h2 class="abs intro-title">REAL HSC COACHING &amp; MENTORING.</h2>
  <p class="abs intro-copy">The HSC help you need, in the years you need it. We offer small classes, individualised attention and genuine care for each student. It'st different - in a good way. Feel free to find out more about us, and let us know if there's any way we can help you on your journey.</p>
  <div class="abs btn-register">Register Now</div>
  <div class="abs intro-art" role="img" aria-label="Green line drawing of study doodles: pencil, books and HSC scribbles"></div>

  <section class="abs panels">
    <div class="panel">
      <h3>What our student says?</h3>
      <div class="quote">
        <div class="avatar" role="img" aria-label="Portrait of the student"></div>
        <p>“Lorem ipsum dolor sit accmet, cec dipiscing elit, sed diam. nxummy nibh euismodunt ut laoreet dolxore magna aliquam erat volutpat. Ut wisi enim ad minim.”</p>
      </div>
      <p class="cite"><b>“Dorian Keller”</b> Elmbank HS</p>
    </div>
    <div class="panel">
      <h3>Free Trial Lesson</h3>
      <div class="trial-box"><div class="l1">Sign Up For</div><div class="l2"><b>Free Trial Class</b> today</div></div>
      <p class="trial-note">Lorem ipsum dolor sit amet consec.</p>
      <p class="trial-link">Send an Enquiry</p>
    </div>
    <div class="panel">
      <div class="news-head">
        <svg width="26" height="20" viewBox="0 0 26 20"><rect x="2" y="3" width="20" height="14" rx="1" fill="#e8e8e8" stroke="#888" transform="rotate(-10 12 10)"/><path d="M6 8h11M6 11h11M6 14h8" stroke="#888" transform="rotate(-10 12 10)"/></svg>
        <h3>Recent News</h3>
      </div>
      <div class="news-item">
        <div class="news-date">20<sup>th</sup><small>FEB</small></div>
        <div>
          <h4>Vulputate velit esse molestie.</h4>
          <p>Lorem ipsum dolor sit consectetuer adipiscing elit, sed diam nonummy nibh euismod tincidunt ut laoreet dolore magna aliquam rat volutpat. Ut wisi enim ad minim.</p>
        </div>
      </div>
    </div>
  </section>

  <section class="abs beliefs">
    <div class="belief">
      <div class="belief-head">
        <svg width="32" height="30" viewBox="0 0 32 30"><rect x="3" y="4" width="27" height="19" fill="none" stroke="#5a9e12" stroke-width="2.5"/><path d="M13 27h8M17 23v4" stroke="#5a9e12" stroke-width="2.5"/><circle cx="8" cy="8" r="5" fill="#555"/><circle cx="15" cy="13" r="3.5" fill="#555"/></svg>
        <h3>We Don't Believe In:</h3>
      </div>
      <ul>
        <li><svg width="14" height="12" viewBox="0 0 14 12"><path d="M2 5v6h9V8" fill="none" stroke="#5a9e12" stroke-width="2"/><path d="M5 7c1-3 3-4 6-4V1l3 3-3 3V5c-2 0-4 1-6 2z" fill="#5a9e12"/></svg>Massive classes;</li>
        <li><svg width="14" height="12" viewBox="0 0 14 12"><path d="M2 5v6h9V8" fill="none" stroke="#5a9e12" stroke-width="2"/><path d="M5 7c1-3 3-4 6-4V1l3 3-3 3V5c-2 0-4 1-6 2z" fill="#5a9e12"/></svg>Spoon-feeding answers;</li>
        <li><svg width="14" height="12" viewBox="0 0 14 12"><path d="M2 5v6h9V8" fill="none" stroke="#5a9e12" stroke-width="2"/><path d="M5 7c1-3 3-4 6-4V1l3 3-3 3V5c-2 0-4 1-6 2z" fill="#5a9e12"/></svg>vOne-size-fits-all teaching.</li>
      </ul>
    </div>
    <div class="belief">
      <div class="belief-head">
        <svg width="36" height="30" viewBox="0 0 36 30"><rect x="2" y="3" width="30" height="20" fill="none" stroke="#5a9e12" stroke-width="2.5"/><path d="M7 9h14M7 13h10M7 17h14" stroke="#555" stroke-width="2"/><path d="M26 16l6 9-3 0 2 4" fill="#555" stroke="#555"/></svg>
        <h3>We Do Believe In:</h3>
      </div>
      <ul>
        <li><svg width="14" height="12" viewBox="0 0 14 12"><path d="M2 5v6h9V8" fill="none" stroke="#5a9e12" stroke-width="2"/><path d="M5 7c1-3 3-4 6-4V1l3 3-3 3V5c-2 0-4 1-6 2z" fill="#5a9e12"/></svg>Small classes tailored to you;</li>
        <li><svg width="14" height="12" viewBox="0 0 14 12"><path d="M2 5v6h9V8" fill="none" stroke="#5a9e12" stroke-width="2"/><path d="M5 7c1-3 3-4 6-4V1l3 3-3 3V5c-2 0-4 1-6 2z" fill="#5a9e12"/></svg>Helping you think for yourself;</li>
        <li><svg width="14" height="12" viewBox="0 0 14 12"><path d="M2 5v6h9V8" fill="none" stroke="#5a9e12" stroke-width="2"/><path d="M5 7c1-3 3-4 6-4V1l3 3-3 3V5c-2 0-4 1-6 2z" fill="#5a9e12"/></svg>Genuinely caring about who you are as an individual.</li>
      </ul>
    </div>
    <div class="belief">
      <div class="belief-head">
        <svg width="32" height="30" viewBox="0 0 32 30"><rect x="3" y="4" width="27" height="19" fill="none" stroke="#5a9e12" stroke-width="2.5"/><path d="M13 27h8M17 23v4" stroke="#5a9e12" stroke-width="2.5"/><circle cx="8" cy="8" r="5" fill="#555"/><circle cx="15" cy="13" r="3.5" fill="#555"/></svg>
        <h3>We Don't Believe In:</h3>
      </div>
      <ul>
        <li><svg width="14" height="12" viewBox="0 0 14 12"><path d="M2 5v6h9V8" fill="none" stroke="#5a9e12" stroke-width="2"/><path d="M5 7c1-3 3-4 6-4V1l3 3-3 3V5c-2 0-4 1-6 2z" fill="#5a9e12"/></svg>Massive classes;</li>
        <li><svg width="14" height="12" viewBox="0 0 14 12"><path d="M2 5v6h9V8" fill="none" stroke="#5a9e12" stroke-width="2"/><path d="M5 7c1-3 3-4 6-4V1l3 3-3 3V5c-2 0-4 1-6 2z" fill="#5a9e12"/></svg>Spoon-feeding answers;</li>
        <li><svg width="14" height="12" viewBox="0 0 14 12"><path d="M2 5v6h9V8" fill="none" stroke="#5a9e12" stroke-width="2"/><path d="M5 7c1-3 3-4 6-4V1l3 3-3 3V5c-2 0-4 1-6 2z" fill="#5a9e12"/></svg>vOne-size-fits-all teaching.</li>
      </ul>
    </div>
  </section>

  <div class="abs tweet">
    <span class="dot"></span><span>|</span>
    <a>@velmorlearns</a>
    <span>This is a tweet from Velmor Learning , you can link your pipstream from here</span>
    <a>lnk.to/Qx7r2</a>
  </div>

  <footer class="abs footer">
    <div class="fcol" style="left:26px">
      <h4>Contact Details</h4>
      <dl>
        <dt>Street:</dt><dd>58 Harlow St Ashvale NSW 2190</dd>
        <dt>Phone:</dt><dd>(02) 5550 3186</dd>
        <dt>Email:</dt><dd>learn@velmorlearning.com.au</dd>
      </dl>
    </div>
    <div class="fcol" style="left:233px">
      <h4>SiteMap</h4>
      <ul><li>Our Associates</li><li>Our Location</li><li>Our Services</li><li>Our Qualifications</li><li>Our Articles</li><li>External Page</li><li>Tell A Friend</li></ul>
    </div>
    <div class="fcol" style="left:352px;width:160px">
      <h4>Testimonials</h4>
      <p>Lorem Ipsum est simplement du fauxtexte employé.</p>
      <p class="name">Dorian Keller</p>
      <p>Lorem Ipsum est simplement du fauxtexte employé.</p>
      <p class="name">Anonymus</p>
    </div>
    <div class="fcol" style="left:544px;width:160px">
      <h4>Sign Up for Newsletter</h4>
      <p style="font-size:8.5px">Lorem Ipsum est simplement du fauxtexte employé</p>
      <div class="email-field">Email Address</div>
      <div class="btn-sub">Subscribe</div>
    </div>
  </footer>

  <div class="abs bottom">
    <span>© Velmor Learning. All rights reserved.</span>
    <nav><span>Home</span><span>About Us</span><span>Courses</span><span>Inspired</span><span>Inspire</span><span>Contact Us</span></nav>
  </div>
</div>
</body>
</html>
```